all natural handmade soap company looking for unique stand out packaging design for bar soaps

we are looking for a unique and stand out on the shelf package design for our hand made soaps for grocery stores. we have a package soap box (picture included) but we are looking for a TOP-NOTCH, CUSTOM, STAND OUT DESIGN FOR THEM. I am supplying our current packaging design, but we want something more unique and STAND OUT. PICTURES i AM INCLUDING ARE: 1: OUR CURRENT PACKAGE DESIGN
2: OUR LIQUID SOAP LABELS (WHICH WE LOVE) AND WOULD LIKE THE BAR SOAPS TO BE SIMILAR
3: WILL BE IN A WHITE BOX WITH A LARGE CUT OUT IN FRONT (SEE SAMPLE BOX BROWN KRAFT).

Target Market(s)

VARIOUS CUSTOMERS. We sell to bright lantern grocers and various grocery stores

Industry/Entity Type

It Company

Requirements
Must have
• cool, unique look that will stand out from a store shelf
• full color acceptable
• our logo on the round part of the package (front)
• please leave a space for bar codes (usually on bottom of box)
• there is a cut out (front) that is there for people to see, feel and smell the soap
• be creative think outside the box open to fresh new designs
Nice to have
• metallic crescent moon (our logo)
Should not have
• organic cannot appear on the front

```html
<!DOCTYPE html>
<html lang="en">
<head>
<meta charset="utf-8">
<title>Lumen Grove – Lemon Natural Soap Box Front</title>
<link rel="stylesheet" href="https://fonts.googleapis.com/css2?family=Arvo:wght@400;700&display=swap">
<style>
  :root {
    --page: #ffffff;
    --mist: #eeeff1;
    --mist-line: #cfd0d3;
    --brand-orange: #f39a1c;
    --ink: #111111;
    --leaf-green: #4b5e2a;
    --sun-yellow: #f6be14;
    --deep-yellow: #e8aa20;
    --band-orange: #f4911e;
    --flame: #ef5a24;
    --silver: #c9cbcf;
  }
  html, body {
    margin: 0;
    padding: 0;
    width: 1200px;
    height: 1200px;
    overflow: hidden;
    background: var(--page);
  }
  .canvas {
    position: relative;
    width: 1200px;
    height: 1200px;
  }
  .box-front {
    position: absolute;
    left: 267px;
    top: 35px;
    width: 665px;
    height: 1130px;
    display: block;
  }
  .brand-name,
  .product-line,
  .tagline,
  .flavour-name,
  .net-weight {
    font-family: "Arvo", Georgia, serif;
  }
  .brand-name { fill: var(--brand-orange); font-size: 54px; font-weight: 400; }
  .product-line { fill: var(--ink); font-size: 30px; }
  .tagline { fill: var(--ink); font-size: 31px; }
  .flavour-name { fill: var(--leaf-green); font-size: 42px; font-weight: 700; letter-spacing: 2px; }
  .net-weight { fill: #ffffff; font-size: 23px; }
</style>
</head>
<body>
<main class="canvas">
  <svg class="box-front" viewBox="0 0 557 947" xmlns="http://www.w3.org/2000/svg" aria-labelledby="box-title">
    <title id="box-title">Lumen Grove lemon natural soap box, front panel</title>
    <defs>
      <linearGradient id="cloud-glow" x1="0" y1="0" x2="0" y2="1">
        <stop offset="0" stop-color="#f8d98f"/>
        <stop offset="1" stop-color="#fbe7bb" stop-opacity="0.6"/>
      </linearGradient>
      <linearGradient id="mist-fade" x1="0" y1="0" x2="0" y2="1">
        <stop offset="0" stop-color="#f2f2f3"/>
        <stop offset="1" stop-color="#e9eaec"/>
      </linearGradient>
      <linearGradient id="lower-yellow" x1="0" y1="0" x2="0" y2="1">
        <stop offset="0" stop-color="var(--deep-yellow)"/>
        <stop offset="1" stop-color="var(--sun-yellow)"/>
      </linearGradient>
      <linearGradient id="swoosh-edge" x1="0" y1="0" x2="1" y2="0">
        <stop offset="0" stop-color="var(--flame)"/>
        <stop offset="0.45" stop-color="#f7a51f"/>
        <stop offset="1" stop-color="#fcd25a"/>
      </linearGradient>
      <radialGradient id="lemon-tone" cx="0.5" cy="0.5" r="0.5">
        <stop offset="0" stop-color="#fbd34a"/>
        <stop offset="0.8" stop-color="#f0b320"/>
        <stop offset="1" stop-color="#f0b320" stop-opacity="0"/>
      </radialGradient>
      <path id="flavour-arc" d="M 148 360 A 140 140 0 0 0 408 360"/>
    </defs>

    <!-- upper sky area -->
    <rect class="sky-panel" x="0" y="0" width="557" height="301" fill="url(#mist-fade)"/>
    <path class="cloud-wash" role="img" aria-label="Soft golden cloud illustration along the top edge"
          d="M0 0 H557 V70 Q500 40 455 60 Q410 20 360 45 Q300 10 240 40 Q180 95 120 80 Q60 130 0 95 Z"
          fill="url(#cloud-glow)"/>

    <!-- round window badge (drawn behind the brand block) -->
    <path class="badge-upper" d="M 99 301 A 179 179 0 0 1 457 301 Z" fill="#ffffff" opacity="0.3"/>
    <line class="sky-divider" x1="0" y1="301" x2="557" y2="301" stroke="var(--mist-line)" stroke-width="2"/>
    <path class="badge-lower" d="M 99 301 A 179 179 0 0 0 457 301 Z" fill="#ffffff"/>
    <path class="badge-rim" d="M 99 301 A 179 179 0 0 0 457 301" fill="none" stroke="var(--mist-line)" stroke-width="3"/>

    <!-- brand block -->
    <circle class="brand-dot" cx="278" cy="108" r="42" fill="var(--silver)"/>
    <text class="brand-name" x="278" y="232" text-anchor="middle">Lumen Grove</text>
    <text class="product-line" x="278" y="274" text-anchor="middle">Natural Soap</text>

    <ellipse class="lemon-art" role="img" aria-label="Illustration of a whole lemon and a halved lemon with green leaves"
             cx="278" cy="352" rx="88" ry="52" fill="url(#lemon-tone)"/>
    <text class="flavour-name"><textPath href="#flavour-arc" startOffset="50%" text-anchor="middle">LEMON</textPath></text>

    <!-- lower sweep -->
    <path class="lower-field" d="M0 593 Q250 715 557 545 V947 H0 Z" fill="url(#lower-yellow)"/>
    <path class="sweep-edge" d="M0 593 Q250 715 557 545 V590 Q300 705 0 600 Z" fill="url(#swoosh-edge)"/>
    <path class="sweep-highlight" d="M150 683 Q380 700 557 658" fill="none" stroke="#ffffff" stroke-width="5" opacity="0.85"/>

    <text class="tagline" x="278" y="793" text-anchor="middle">Handcrafted</text>
    <text class="tagline" x="278" y="836" text-anchor="middle">Artsan Natural Soap</text>

    <rect class="weight-band" x="0" y="898" width="557" height="49" fill="var(--band-orange)"/>
    <text class="net-weight" x="278" y="932" text-anchor="middle">4.5oz ( 127.57 grams )</text>
  </svg>
</main>
</body>
</html>
```